Quote Cards With KB May 2025 for Instagram

I would like to put these quotes over one of the pictures attached; Instagram (new size: 4:5 (1080 x 1350 pixels) One Quote per picture, and I want the quote to be bold or easy to read as well. I provided a few reference graphics that I really like as examples below. In very small letters at the bottom add @KBHarlowOnline

All of the pictures are attached; you can pick any photo and add one quote to it; but no stock photography

```html
<!DOCTYPE html>
<html lang="en">
<head>
<meta charset="utf-8">
<title>Quote Cards With KB — May 2025</title>
<link rel="stylesheet" href="https://fonts.googleapis.com/css2?family=League+Gothic&family=Roboto+Condensed:wght@300;400;500;700&family=Montserrat:wght@500;700&display=swap">
<style>
  :root{
    --page:#f2f2f2;
    --white:#ffffff;
    --ink:#1d1a1f;
    --magenta:#c3228e;
    --peach:#f8d5c2;
    --plum:#8a3f78;
  }
  *{box-sizing:border-box;margin:0;padding:0}
  html,body{width:1200px;height:3217px;overflow:hidden;background:var(--page)}
  .board{position:relative;width:1200px;height:3217px}
  .card{position:absolute;width:460px;height:575px;overflow:hidden}
  .col-a{left:120px}.col-b{left:620px}
  .row-1{top:81px}.row-2{top:693px}.row-3{top:1307px}.row-4{top:1929px}.row-5{top:2560px}
  .photo{position:absolute;inset:0}
  .panel{position:absolute;top:0;bottom:0;width:246px}
  .panel.left{left:0}.panel.right{right:0;width:247px}
  .block{position:absolute;left:18px;width:226px;color:var(--white);white-space:nowrap}
  .block.in-right{left:231px;width:224px}
  .headline{font-family:"League Gothic",sans-serif;font-weight:400;letter-spacing:0}
  .headline .line{display:block}
  .body{font-family:"Roboto Condensed",sans-serif;font-weight:500}
  .cta{font-family:"Montserrat",sans-serif;font-weight:700}
  .light{font-weight:300}
  .strong{font-weight:700}
  .handle{position:absolute;bottom:12px;height:20px;font-family:"Montserrat",sans-serif;font-weight:500;font-size:15px;line-height:20px;color:var(--white);text-align:center}
  .handle.on-right{left:246px;right:0}
  .handle.on-left{left:0;width:213px}
</style>
</head>
<body>
<main class="board">

  <section class="card col-a row-1">
    <div class="photo" role="img" aria-label="Woman in a long pink gown on a stage with purple lights" style="background:linear-gradient(135deg,#b0267f,#6a2a8e 60%,#d35a3b)"></div>
    <div class="panel left" style="background:linear-gradient(180deg,#a72a9a,#c4247a)"></div>
    <div class="block headline" style="top:34px;font-size:66px;line-height:66px">Tired.<br>Moody.<br>Stubborn<br>Belly Fat.</div>
    <div class="block body" style="top:334px;font-size:34px;line-height:45px">Your hormones<br>are screaming<br>for help!</div>
    <div class="block cta" style="top:500px;font-size:25px">Let’s fix that.</div>
    <div class="handle on-right" style="background:var(--magenta)">@KBHarlowOnline</div>
  </section>

  <section class="card col-b row-1">
    <div class="photo" role="img" aria-label="Woman in a sparkly bodysuit and black jeans on a basketball court" style="background:linear-gradient(180deg,#3b3a4a,#7a5a3a 60%,#c89a3a)"></div>
    <div class="panel left" style="background:rgba(106,88,72,.92)"></div>
    <div class="block headline" style="top:40px;font-size:58px;line-height:59px">That stubborn<br>weight?<br>It’s not your<br>fault.</div>
    <div class="block body" style="top:300px;font-size:33px;line-height:44px">Your hormones<br>are to blame<br>and you’re not<br>alone;</div>
    <div class="block cta" style="top:527px;font-size:21px">But there is a fix.</div>
    <div class="handle on-right" style="background:rgba(60,50,40,.8)">@KBHarlowOnline</div>
  </section>

  <section class="card col-a row-2">
    <div class="photo" role="img" aria-label="Woman in a black sheer top standing outdoors among green hills" style="background:linear-gradient(180deg,#b8c8d6,#7d8a6a 60%,#3c4a2e)"></div>
    <div class="panel right" style="background:rgba(93,97,99,.93)"></div>
    <div class="block headline in-right" style="top:36px">
      <span class="line" style="font-size:68px;line-height:68px">Your belly</span>
      <span class="line" style="font-size:68px;line-height:68px">isn’t fat…</span>
      <span class="line" style="font-size:56px;line-height:62px">it’s hormonal.</span>
    </div>
    <div class="block body in-right" style="top:262px;font-size:35px;line-height:47px">And here’s<br>how to fix it.<br><span class="light">Comment</span><br><span class="strong" style="font-size:39px">HORMONES</span><br><span class="light">if nothing is<br>working.</span></div>
    <div class="handle on-left" style="background:rgba(0,0,0,.85)">@KBHarlowOnline</div>
  </section>

  <section class="card col-b row-2">
    <div class="photo" role="img" aria-label="Woman in a sheer black outfit indoors with a city night view" style="background:linear-gradient(180deg,#1c2540,#2b3450 55%,#8a7458)"></div>
    <div class="panel right" style="background:rgba(78,65,57,.94)"></div>
    <div class="block headline in-right" style="top:26px">
      <span class="line" style="font-size:56px;line-height:60px">The stubborn</span>
      <span class="line" style="font-size:92px;line-height:86px">belly fat</span>
      <span class="line" style="font-size:56px;line-height:60px">after 40?</span>
    </div>
    <div class="block body in-right" style="top:298px;font-size:33px;line-height:45px">It’s not about<br>calories;<br>it’s about your<br>hormones.</div>
    <div class="block cta in-right" style="top:518px;font-size:25px">Here is the fix!</div>
    <div class="handle on-left" style="background:rgba(0,0,0,.85)">@KBHarlowOnline</div>
  </section>

  <section class="card col-a row-3">
    <div class="photo" role="img" aria-label="Woman in a striped sheer top posing in a bright white room" style="background:linear-gradient(160deg,#e8e6e2,#b9b4ae 55%,#2a2a2c)"></div>
    <div class="panel left" style="background:rgba(80,80,82,.9)"></div>
    <div class="block headline" style="top:32px;font-size:64px;line-height:63px">Flat tummy<br>in your 40s?</div>
    <div class="block body" style="top:204px;font-size:28px;line-height:40px">It’s still possible!<br>Comment<br><span class="strong" style="font-size:44px;line-height:54px">BYE BELLY</span><br>to get the 10<br>secrets to a<br>flatter tummy</div>
    <div class="handle on-right" style="background:rgba(0,0,0,.85)">@KBHarlowOnline</div>
  </section>

  <section class="card col-b row-3">
    <div class="photo" role="img" aria-label="Woman in a white cropped sweater pointing upward" style="background:linear-gradient(180deg,#f2f2f4,#d9d6de 60%,#2a2a30)"></div>
    <div class="panel left" style="background:linear-gradient(180deg,#efedf2,#d9d1ea)"></div>
    <div class="block headline" style="top:32px;font-size:58px;line-height:56px;color:var(--ink)">Bloating.<br>Muffin top.<br>Puffy waistline.</div>
    <div class="block body" style="top:235px;font-size:35px;line-height:46px;color:var(--ink)">Your body’s<br>screaming for<br>a different<br>kind of fix</div>
    <div class="block cta" style="top:490px;font-size:27px;color:var(--ink)">Here it is</div>
    <div class="handle on-right" style="background:var(--white);color:var(--ink)">@KBHarlowOnline</div>
  </section>

  <section class="card col-a row-4">
    <div class="photo" role="img" aria-label="Woman in a pink knit dress beside sunflowers and neon lights" style="background:linear-gradient(180deg,#6a7a8a,#a89a7a 50%,#c9a23a)"></div>
    <div class="panel right" style="background:rgba(162,108,138,.92)"></div>
    <div class="block headline in-right" style="top:28px;font-size:50px;line-height:48px">You’re doing<br>all the “right”<br>things, but your<br>belly won’t go<br>down?</div>
    <div class="block body in-right" style="top:335px;font-size:40px;line-height:51px;color:var(--peach)">Here’s what<br>you haven’t<br>tried.</div>
    <div class="handle on-left" style="background:var(--white);color:var(--ink)">@KBHarlowOnline</div>
  </section>

  <section class="card col-b row-4">
    <div class="photo" role="img" aria-label="Woman in a pink top holding a basketball courtside" style="background:linear-gradient(180deg,#2a3a7a,#4a4150 55%,#1e1e24)"></div>
    <div class="panel right" style="background:rgba(138,63,120,.92)"></div>
    <div class="block headline in-right" style="top:36px">
      <span class="line" style="font-size:50px;line-height:52px">This 90-day plan</span>
      <span class="line" style="font-size:50px;line-height:50px">helped women</span>
      <span class="line" style="font-size:44px;line-height:46px">over 40 slim down,</span>
    </div>
    <div class="block body in-right" style="top:235px;font-size:40px;line-height:52px;color:var(--peach)">Get a tiny<br>waist and<br>feel sexy<br>again.</div>
    <div class="block cta in-right" style="top:508px;font-size:25px;color:var(--peach)">You’re next.</div>
    <div class="handle on-left" style="background:var(--plum)">@KBHarlowOnline</div>
  </section>

  <section class="card col-a row-5">
    <div class="photo" role="img" aria-label="Smiling woman in a black top and jeans on a sunny hillside" style="background:linear-gradient(180deg,#a8c4e0,#8a9a8a 55%,#2a2a2e)"></div>
    <div class="panel left" style="background:rgba(74,77,82,.9)"></div>
    <div class="block headline" style="top:36px;font-size:45px;line-height:43px">This is the secret<br>women over 40<br>are using to get<br>snatched;<br>without starving.</div>
    <div class="block body" style="top:300px;font-size:35px;line-height:46px">Comment<br><span class="strong" style="font-size:54px;line-height:60px">SKINNY</span><br>to get the<br>exact plan.</div>
    <div class="handle on-right" style="background:rgba(0,0,0,.85)">@KBHarlowOnline</div>
  </section>

  <section class="card col-b row-5">
    <div class="photo" role="img" aria-label="Woman in a black open-back top looking over her shoulder" style="background:linear-gradient(180deg,#d8d6d4,#9a9694 50%,#2c2a2a)"></div>
    <div class="panel left" style="background:rgba(60,62,66,.92)"></div>
    <div class="block headline" style="top:38px;font-size:54px;line-height:53px">What worked<br>in your 30s<br>won’t work<br>now.</div>
    <div class="block body" style="top:300px;font-size:34px;line-height:45px">Here’s what<br>actually does.<br>Drop 30<br>Pounds in 3<br>Months.</div>
    <div class="handle on-right" style="background:rgba(0,0,0,.85)">@KBHarlowOnline</div>
  </section>

</main>
</body>
</html>
```